Building company buisness cards

We are looking for a sharp modern new look for our business cards.
We are a New Zealand based company that specialises in house and land packages.
We have attached a photo of the current logo and would like to see if it can be improved somehow if needed.
We are open to any colours but we have chosen green at this stage.
Feel free to change the font and make the logo smarter looking.
Play with the colours and see what looks best.

We want a card that looks so good know one will want to throw it away!

Target Market(s)

Home buyers

Industry/Entity Type

Building

Contact Information for Business Card

Derek Tolvane
0217394062
dtolvane@quillmarkhomesteads.co.nz
quillmarkhomesteads.co.nz

Font styles to use
Serif
Sans Serif

Colors

Designer to choose colors to be used in the design.

Requirements
Must have
• Logo and company name on one side, details on the other side
Nice to have
• Color codes for the original green are HEX #4a8028, RGB(74,128,40), CMYK(42,0,69,50)
• Round corners, Raised and/or spot UV

```html
<!DOCTYPE html>
<html lang="en">
<head>
<meta charset="utf-8">
<title>Quillmark Homesteads – Business Cards</title>
<link rel="stylesheet" href="https://fonts.googleapis.com/css2?family=Roboto:wght@300;400&display=swap">
<style>
  :root {
    --brand-green: #4a8028;
    --paper: #f7f7f5;
    --backdrop: #e6e6e6;
    --white: #ffffff;
    --rule-light: rgba(255,255,255,0.75);
    --rule-green: rgba(74,128,40,0.45);
  }
  * { box-sizing: border-box; margin: 0; padding: 0; }
  html, body {
    width: 1200px; height: 571px; overflow: hidden;
    background: var(--backdrop);
  }
  .stage {
    position: relative; width: 1200px; height: 571px;
    display: flex; align-items: center; justify-content: center; gap: 60px;
  }
  .card {
    width: 480px; height: 267px; border-radius: 10px;
    position: relative;
    box-shadow: 0 6px 18px rgba(0,0,0,0.12);
    font-family: "Roboto", sans-serif;
  }
  .company-name {
    font-family: "Roboto", sans-serif; font-weight: 400;
    line-height: 1; white-space: nowrap;
  }
  /* Details side */
  .card--details {
    background: var(--brand-green); color: var(--white);
    padding: 52px 40px 0 48px;
  }
  .card--details .company-name { font-size: 22px; color: var(--white); }
  .contact {
    margin-top: 24px;
    border-left: 1px solid var(--rule-light);
    padding-left: 18px;
  }
  .contact__name {
    font-weight: 300; font-size: 22px; letter-spacing: 0.5px;
    text-transform: uppercase; line-height: 1;
  }
  .contact__role { font-weight: 300; font-size: 12px; margin-top: 4px; }
  .contact__list { list-style: none; margin-top: 14px; }
  .contact__item {
    display: flex; align-items: center; gap: 10px;
    font-weight: 300; font-size: 12.5px; line-height: 1; margin-bottom: 7px;
  }
  .contact__icon { width: 11px; height: 11px; flex: none; }
  /* Logo side */
  .card--logo {
    background: var(--paper);
    display: flex; flex-direction: column; align-items: center; justify-content: center;
  }
  .card--logo .company-name { font-size: 32px; color: var(--brand-green); }
  .logo-rule {
    width: 60px; height: 1px; background: var(--rule-green); margin-top: 16px;
  }
</style>
</head>
<body>
<main class="stage">
  <section class="card card--details" aria-label="Contact side">
    <p class="company-name">Quillmark Homesteads</p>
    <div class="contact">
      <p class="contact__name">Derek Tolvane</p>
      <p class="contact__role">Founder &amp; CEO</p>
      <ul class="contact__list">
        <li class="contact__item">
          <svg class="contact__icon" viewBox="0 0 16 16" aria-hidden="true"><path fill="#fff" d="M3.6 1.5l2.3 2.8-1.4 1.7c.9 2 2.5 3.6 4.5 4.5l1.7-1.4 2.8 2.3-1.3 2.1C7 13.1 2.9 9 2.5 3.1z"/></svg>
          <span>0217394062</span>
        </li>
        <li class="contact__item">
          <svg class="contact__icon" viewBox="0 0 16 16" aria-hidden="true"><rect x="1" y="3" width="14" height="10" rx="1" fill="#fff"/><path d="M1.5 3.8L8 9l6.5-5.2" fill="none" stroke="#4a8028" stroke-width="1.4"/></svg>
          <span>dtolvane@quillmarkhomesteads.co.nz</span>
        </li>
        <li class="contact__item">
          <svg class="contact__icon" viewBox="0 0 16 16" aria-hidden="true"><circle cx="8" cy="8" r="6.5" fill="none" stroke="#fff" stroke-width="1.4"/><ellipse cx="8" cy="8" rx="2.8" ry="6.5" fill="none" stroke="#fff" stroke-width="1.2"/><path d="M1.5 8h13" stroke="#fff" stroke-width="1.2"/></svg>
          <span>www.quillmarkhomesteads.co.nz</span>
        </li>
      </ul>
    </div>
  </section>

  <section class="card card--logo" aria-label="Name side">
    <p class="company-name">Quillmark Homesteads</p>
    <div class="logo-rule"></div>
  </section>
</main>
</body>
</html>
```